Redesign website for small print company

Vindurgata is a small printing company in Iceland mainly servicing Students, schools, etc. We are also doing all kind of other jobs, like business cards, book printing, brochure printing etc. We are also selling books online.
Our website is: www.vindurgata.is
What we are looking for is:
- Web Design (Uncoded - PSD layout only)
- Mobile friendly design, using our current color scheme: Red, green, yellow and light gray.
- Clean simple design
- Simple, light and easy to use.
- More menu Items/drop down
Industry/Entity Type
Digital Printing
Number of Pages Required
5+ page
Requirements
Must have
- Easy navigation
- Designed for mobile
- Current color scheme (see logo)
Nice to have
- Icon based products

```html
<!DOCTYPE html>
<html lang="en">
<head>
<meta charset="utf-8">
<title>Vindurgata – Printing for students and schools</title>
<link rel="stylesheet" href="https://fonts.googleapis.com/css2?family=Montserrat:wght@400;500;600&display=swap">
<style>
:root{
  --red:#e8262a;
  --yellow:#fdc811;
  --green:#0f5a25;
  --dark:#2a2a2a;
  --text:#333;
  --white:#fff;
  --grey:#f2f2f2;
  --head:'Montserrat',sans-serif;
  --body:Arial,Helvetica,sans-serif;
}
*{margin:0;padding:0;box-sizing:border-box}
html,body{width:1200px;height:2711px;overflow:hidden;background:var(--white)}
body{position:relative;font-family:var(--body);color:var(--text)}
.abs{position:absolute}

.top-bar{left:0;top:0;width:1200px;height:6px;background:var(--yellow)}
.site-header{left:0;top:6px;width:1200px;height:97px;background:var(--white)}
.brand{left:87px;top:34px;display:flex;align-items:center;gap:10px;font-family:var(--head);font-weight:600;font-size:27px;color:#111;letter-spacing:.3px}
.brand-mark{width:30px;height:30px;background:var(--red)}
.main-nav{left:0;top:46px;font-family:var(--head);font-weight:500;font-size:12.5px;color:#222;text-transform:uppercase}
.main-nav span{position:absolute;white-space:nowrap;top:0}
.main-nav .active{color:var(--red)}
.icon-btn{top:31px;width:44px;height:44px;border-radius:50%;border:2px solid;display:flex;align-items:center;justify-content:center}
.icon-btn.search{left:1016px;border-color:var(--red)}
.icon-btn.cart{left:1068px;border-color:var(--yellow)}

.dropdown{left:500px;top:87px;width:197px;height:220px;background:var(--red);z-index:5;padding:22px 0 0 29px;font-family:var(--head);font-weight:500;font-size:14.5px;color:var(--white)}
.dropdown::before{content:"";position:absolute;left:20px;top:-8px;border:8px solid transparent;border-top:0;border-bottom-color:var(--red)}
.dropdown li{list-style:none;height:32px}

.hero{left:0;top:103px;width:1200px;height:562px;background:radial-gradient(circle at 18% 20%,#1c4ed8 0,transparent 22%),radial-gradient(circle at 48% 10%,#ffd400 0,transparent 14%),radial-gradient(circle at 75% 5%,#28c24c 0,transparent 18%),radial-gradient(circle at 6% 15%,#e52272 0,transparent 14%),linear-gradient(180deg,#33303c,#17161c)}
.hero-title{left:628px;top:360px;font-family:var(--head);font-weight:500;font-size:64px;color:var(--yellow)}
.hero-text{left:632px;top:448px;width:440px;font-size:12.5px;line-height:29px;color:var(--white)}
.btn-yellow{left:633px;top:553px;width:141px;height:48px;border-radius:24px;background:var(--yellow);color:var(--white);font-family:var(--head);font-weight:500;font-size:15px;display:flex;align-items:center;justify-content:center}
.slide-arrow{top:367px;width:34px;height:34px;border:1.5px solid var(--white);border-radius:50%;display:flex;align-items:center;justify-content:center}

.section-title{left:0;width:1200px;text-align:center;font-family:var(--head);font-weight:500;color:#222}
.services-sub{left:0;top:752px;width:1200px;text-align:center;font-size:12px}
.service{width:290px;text-align:center}
.service .badge{width:150px;height:150px;margin:0 auto;border-radius:50%;display:flex;align-items:center;justify-content:center}
.service h3{font-family:var(--head);font-weight:500;font-size:23px;margin-top:26px}
.service p{font-size:12px;line-height:26px;margin-top:6px;padding:0 10px}
.bg-red{background:var(--red)}.bg-yellow{background:var(--yellow)}.bg-green{background:var(--green)}
.c-red{color:var(--red)}.c-yellow{color:var(--yellow)}.c-green{color:var(--green)}

.submission{left:0;top:1495px;width:1200px;height:373px;background:linear-gradient(115deg,#d42a1c 0%,#f0521f 35%,#f59b16 65%,#f3c919 100%)}
.submission h2{position:absolute;left:0;top:62px;width:1200px;text-align:center;font-family:var(--head);font-weight:500;font-size:40px;color:var(--white)}
.submission p{position:absolute;left:240px;top:136px;width:720px;text-align:center;font-size:12.5px;line-height:27px;color:var(--white)}
.btn-outline{left:482px;top:244px;width:236px;height:49px;border:2px solid var(--white);border-radius:25px;color:var(--white);font-family:var(--head);font-weight:500;font-size:12.5px;display:flex;align-items:center;justify-content:center}

.about-title{left:87px;top:1932px;font-family:var(--head);font-weight:500;font-size:29px;color:#222}
.about-text{left:87px;width:545px;font-size:12.2px;line-height:27.5px;color:#222}
.about-photo{left:700px;top:1895px;width:395px;height:370px;background:radial-gradient(ellipse at 50% 60%,#d9c9a8 0,#eee7da 45%,#fff 75%)}

.site-footer{left:0;top:2330px;width:1200px;height:381px;background:var(--dark);color:var(--white)}
.map{left:87px;top:45px;width:325px;height:220px;background:linear-gradient(120deg,#a9d3f5 0 38%,#ecebe6 38% 100%);border:3px solid #fff}
.foot-head{top:42px;font-family:var(--head);font-weight:500;font-size:20px}
.foot-text{font-size:14.5px;line-height:19px}
.foot-links{left:684px;top:92px;font-size:14.5px;list-style:none}
.foot-links li{height:30px}
.email-field{left:846px;top:85px;width:264px;height:37px;background:var(--white);color:#333;font-family:var(--head);font-size:11px;padding:13px 14px}
.btn-subscribe{left:846px;top:132px;width:126px;height:36px;background:var(--yellow);color:var(--white);font-size:14px;display:flex;align-items:center;justify-content:center}
.social{top:189px;width:22px;height:22px;border-radius:50%;border:2px solid var(--white)}
.foot-rule{left:87px;top:310px;width:1026px;height:1px;background:#555}
.copyright{left:0;top:340px;width:1200px;text-align:center;font-size:12.5px}
</style>
</head>
<body>

<div class="abs top-bar"></div>
<header class="abs site-header">
  <div class="abs brand"><span class="brand-mark"></span>VINDURGATA</div>
  <nav class="abs main-nav">
    <span class="active" style="left:410px">Home</span>
    <span style="left:501px">Services</span>
    <span style="left:613px">Submission of works</span>
    <span style="left:812px">About us</span>
    <span style="left:928px">Contact us</span>
  </nav>
  <div class="abs icon-btn search"><svg width="14" height="14" viewBox="0 0 14 14"><circle cx="6" cy="6" r="4" fill="none" stroke="#e8262a" stroke-width="2"/><line x1="9" y1="9" x2="13" y2="13" stroke="#e8262a" stroke-width="2"/></svg></div>
  <div class="abs icon-btn cart"><svg width="14" height="14" viewBox="0 0 14 14"><path d="M1 2h2l2 7h7l1-5H4" fill="none" stroke="#fdc811" stroke-width="1.6"/><circle cx="6" cy="12" r="1.2" fill="#fdc811"/><circle cx="11" cy="12" r="1.2" fill="#fdc811"/></svg></div>
</header>

<ul class="abs dropdown">
  <li>Essays</li><li>Business cards</li><li>Pamphlets</li><li>Book Printing</li><li>Posters</li><li>Textbooks</li>
</ul>

<section class="abs hero" role="img" aria-label="Dripping paint in blue, pink, yellow and green on a dark background"></section>
<div class="abs slide-arrow" style="left:42px"><svg width="10" height="12"><path d="M7 1 2 6l5 5" fill="none" stroke="#fff" stroke-width="2"/></svg></div>
<div class="abs slide-arrow" style="left:1122px"><svg width="10" height="12"><path d="M3 1l5 5-5 5" fill="none" stroke="#fff" stroke-width="2"/></svg></div>
<h1 class="abs hero-title">Vindurgata</h1>
<p class="abs hero-text">University education is a company located in the campus, which has specialized in the service of school staff, as well as providing general public printing. Higher education publishes seminars and first-class textbooks</p>
<div class="abs btn-yellow">READ MORE</div>

<h2 class="abs section-title" style="top:704px;font-size:29px">OUR SERVICES</h2>
<p class="abs services-sub">University education is a company located in the campus, which has specialized in the service of school staff</p>

<div class="abs service" style="left:105px;top:818px">
  <div class="badge bg-red"><svg width="60" height="60" viewBox="0 0 60 60" fill="none" stroke="#fff" stroke-width="2.5"><rect x="12" y="8" width="30" height="42"/><path d="M18 20h14M18 28h12M18 36h10M36 44l16-20"/></svg></div>
  <h3 class="c-red">Essays</h3>
  <p>We recommend that students come to us to see proof of paper before printing, to ensure that every thing is as best as possible.</p>
</div>
<div class="abs service" style="left:455px;top:818px">
  <div class="badge bg-yellow"><svg width="60" height="60" viewBox="0 0 60 60" fill="none" stroke="#fff" stroke-width="2.5"><rect x="8" y="16" width="34" height="22" rx="3"/><rect x="18" y="24" width="34" height="22" rx="3"/><path d="M24 32h12M24 38h20"/></svg></div>
  <h3 class="c-yellow">Business cards</h3>
  <p>We recommend that students come to us to see proof of paper before printing, to ensure that every thing is as best as possible.</p>
</div>
<div class="abs service" style="left:805px;top:818px">
  <div class="badge bg-green"><svg width="60" height="60" viewBox="0 0 60 60" fill="none" stroke="#fff" stroke-width="2.5"><path d="M10 14l13-4 14 4 13-4v36l-13 4-14-4-13 4z"/><path d="M23 10v36M37 14v36"/></svg></div>
  <h3 class="c-green">Pamphlets</h3>
  <p>We recommend that students come to us to see proof of paper before printing, to ensure that every thing is as best as possible.</p>
</div>
<div class="abs service" style="left:105px;top:1162px">
  <div class="badge bg-yellow"><svg width="60" height="60" viewBox="0 0 60 60" fill="none" stroke="#fff" stroke-width="2.5"><rect x="18" y="8" width="30" height="38"/><rect x="12" y="16" width="30" height="38"/><path d="M18 44l8-10 6 6 4-4 6 8"/></svg></div>
  <h3 class="c-yellow">Book Printing</h3>
  <p>We recommend that students come to us to see proof of paper before printing, to ensure that every thing is as best as possible.</p>
</div>
<div class="abs service" style="left:455px;top:1162px">
  <div class="badge bg-green"><svg width="60" height="60" viewBox="0 0 60 60" fill="none" stroke="#fff" stroke-width="2.5"><rect x="14" y="12" width="32" height="42"/><circle cx="30" cy="8" r="3"/><path d="M20 44l7-12 5 7 4-5 5 10z"/></svg></div>
  <h3 class="c-green">Posters</h3>
  <p>We recommend that students come to us to see proof of paper before printing, to ensure that every thing is as best as possible.</p>
</div>
<div class="abs service" style="left:805px;top:1162px">
  <div class="badge bg-red"><svg width="60" height="60" viewBox="0 0 60 60" fill="none" stroke="#fff" stroke-width="2.5"><path d="M6 14h20l4 4 4-4h20v32H34l-4 4-4-4H6z"/><path d="M30 18v32M12 24h12M12 30h12M36 24h12M36 30h12"/></svg></div>
  <h3 class="c-red">Textbooks</h3>
  <p>We recommend that students come to us to see proof of paper before printing, to ensure that every thing is as best as possible.</p>
</div>

<section class="abs submission">
  <h2>SUBMISSION OF WORKS</h2>
  <p>There are various ways to send us a project, you can submit content evenly to paper as a computerized form, a CD or a memory stick, whatever suits you best.A common way is to send a project by e-mail at work@vindurgata.is. You can also upload documents to our data server below. (If documents are large, we strongly recommend using the data server)</p>
  <div class="abs btn-outline">CLICK HERE FOR MORE INFO</div>
</section>

<h2 class="abs about-title">ABOUT OUR VINDURGATA</h2>
<p class="abs about-text" style="top:2008px">University education is a company located in the campus, which has specialized in the service of school staff, as well as providing general public printing.Higher education publishes seminars and first-class textbooks for courses, prints theses for lesson, as well as working on an unprecedented number of smaller pieces for students, teachers and organiza questionnaires</p>
<p class="abs about-text" style="top:2146px">Business cards, books, OCR scanning and more.Higher education is a tailored print shop, The Leaf is the official eco-label of the Nordic countries, which has created a foothold in this country and is known among consumers.University education is located at the corner of Hrafnagata and Austurgata. (walked into Austurgötumegin)</p>
<div class="abs about-photo" role="img" aria-label="Group of cheerful students holding books and folders"></div>

<footer class="abs site-footer">
  <div class="abs map" role="img" aria-label="Street map showing the shop location"></div>
  <h4 class="abs foot-head" style="left:455px">CONTACT US</h4>
  <div class="abs foot-text" style="left:455px;top:94px">ADDRESS<br>24 Harbour Lane #B<br>Reykjavik 101 IS</div>
  <div class="abs foot-text" style="left:455px;top:170px">PHONE<br>555 0142</div>
  <div class="abs foot-text" style="left:455px;top:227px">EMAIL<br>verk@vindurgata.is</div>
  <h4 class="abs foot-head" style="left:678px">COMPANY</h4>
  <ul class="abs foot-links"><li>Home</li><li>Services</li><li>Submission of works</li><li>About us</li><li>Contact us</li></ul>
  <h4 class="abs foot-head" style="left:845px">KEEP IN TOUCH</h4>
  <div class="abs email-field">EMAIL ADDRESS</div>
  <div class="abs btn-subscribe">SUBSCRIBE</div>
  <span class="abs social" style="left:855px" aria-label="Social link"></span>
  <span class="abs social" style="left:902px" aria-label="Social link"></span>
  <span class="abs social" style="left:948px" aria-label="Social link"></span>
  <div class="abs foot-rule"></div>
  <p class="abs copyright">© Copyright 2018 Vindurgata. All rightt reserved</p>
</footer>

</body>
</html>
```